Website for courses for men for making money, health, fitness

I require a website which is going to be a mix of a crypto currency website and website aimed at providing men with money making, health, relationship advice courses and content

The name isn't decided yet so for now please call it something like

KESTREL YARD

A platform dedicated to making men wealthy, physically strong, mentally tough & successful with women

In the top right, I need it to show how many points they have, they must buy points in order to use them to claim the courses.

WHAT WE DO

Kestrel yard is a platform where you can learn everything you need about business, making money, crypto currency, fitness, health, mental toughness and resilience and how to be successful with women all in one place

HOW WILL THIS WORK & WHY SHOULD I BUY POINTS?

xxxxxxxxxxxxxxxxxxxxxxxx
xxxxxxxxxxxxxxxxxxxxxxx
xxxxxxxxxxxxxxxxxxxxx

AFFILIATE SCHEME

EARN UP TO $125 DOLLARS PER PERSON WHO SIGNS UP THROUGH YOUR LINK

START EARNING NOW - button
______________________________________________________

BUY POINTS
(A maximum of only $250 worth of points can be purchased per person until the platform goes fully live)

ROAD MAP & THE MODEL

2023

Q1 - PRE BUY IN FOR POINTS

Q2 - FULL WEBSITE LAUNCH

Q3 - APP LAUNCH

Q4 - IN APP ADVERT LAUNCH

It must have a very slick and sharp eye catching look, and be designed to convert people into purchasing points

some ideas of the feel of the website -

https://brivaloo.io/
https://nestorly.style/
https://plumwick.trelvanta.com/

```html
<!DOCTYPE html>
<html lang="en">
<head>
<meta charset="utf-8">
<title>Kestrel Yard</title>
<link rel="stylesheet" href="https://fonts.googleapis.com/css2?family=Michroma&family=Open+Sans:wght@400;600;700&display=swap">
<style>
  :root{
    --bg:#0a0a1d;
    --bg-deep:#07071a;
    --footer:#0b0b22;
    --accent:#2a16c4;
    --accent-bright:#3a22e0;
    --accent-line:#3b26d8;
    --halo:#15123f;
    --text:#ffffff;
    --muted:#e4e4f0;
    --dots:#c9c9e0;
  }
  *{margin:0;padding:0;box-sizing:border-box}
  html,body{width:1200px;height:4409px;overflow:hidden}
  body{
    position:relative;
    background:radial-gradient(ellipse at 90% 3%, #2a1140 0, transparent 22%),
               linear-gradient(180deg,var(--bg-deep) 0,var(--bg) 30%,var(--bg) 100%);
    color:var(--text);
    font-family:"Open Sans",sans-serif;
  }
  .abs{position:absolute}
  .display{font-family:"Michroma",sans-serif;font-weight:400;letter-spacing:1px}
  .btn{
    position:absolute;display:flex;align-items:center;justify-content:center;
    background:var(--accent);border:2px solid var(--accent-bright);border-radius:26px;
    font-weight:700;font-size:17px;color:var(--text);
  }
  .rule{position:absolute;width:44px;height:4px;background:var(--accent-line)}
  .body-copy{font-size:14.5px;line-height:26px;color:var(--muted)}
  .center{text-align:center;left:0;width:1200px}

  /* nav */
  .brand{font-family:"Michroma",sans-serif;font-size:30px;letter-spacing:1px;color:var(--text)}
  .nav-link{position:absolute;top:53px;font-size:15px}
  .nav-link.active{font-weight:700;text-decoration:underline;text-underline-offset:4px}
  .points-pill{
    position:absolute;left:834px;top:38px;width:146px;height:51px;border:2px solid var(--accent-bright);
    border-radius:26px;display:flex;align-items:center;justify-content:center;gap:10px;font-size:15px
  }

  .hero-art{left:514px;top:103px;width:607px;height:453px;
    background:radial-gradient(circle at 55% 45%, #1a3a8a 0, #141c4a 35%, transparent 70%),
               radial-gradient(ellipse at 50% 90%, #b58a1c 0, #5a3d0c 25%, transparent 55%);
    clip-path:polygon(10% 100%,0 70%,18% 20%,50% 0,85% 10%,100% 60%,92% 100%)}
  .photo-hex{position:absolute}

  .road-title{font-family:"Michroma",sans-serif;font-size:21px}
  .road-sub{font-size:20px;font-weight:700;margin-top:10px}
  .road-desc{font-size:14.5px;line-height:26px;color:var(--muted);margin-top:2px}
  .road-text{position:absolute;width:640px}
  .road-bar{position:absolute;width:3px;height:125px;background:var(--accent-line)}

  .footer{position:absolute;left:0;top:4006px;width:1200px;height:403px;background:var(--footer)}
  .footer-links{position:absolute;top:212px;left:0;width:1200px;display:flex;justify-content:center;gap:46px;font-size:17px}
  .socials{position:absolute;top:268px;left:0;width:1200px;display:flex;justify-content:center;gap:20px}
  .socials span{width:38px;height:38px;border-radius:50%;background:var(--accent)}
  .copyright{position:absolute;top:333px;left:0;width:1200px;text-align:center;font-size:17px;font-weight:600}
</style>
</head>
<body>

<!-- navigation -->
<header>
  <div class="abs brand" style="left:80px;top:44px">KESTREL YARD</div>
  <span class="nav-link active" style="left:507px">Home</span>
  <span class="nav-link" style="left:595px">What We Do</span>
  <span class="nav-link" style="left:727px">Contact Us</span>
  <div class="points-pill">Points&nbsp; $15
    <svg width="22" height="22" viewBox="0 0 22 22" fill="none" stroke="#fff" stroke-width="1.5"><ellipse cx="9" cy="5" rx="6" ry="2.5"/><path d="M3 5v10c0 1.4 2.7 2.5 6 2.5M15 5v3"/><circle cx="15" cy="15" r="5"/></svg>
  </div>
  <div class="btn" style="left:1000px;top:38px;width:116px;height:51px;font-size:16px">Buy Points</div>
</header>

<!-- hero -->
<section>
  <div class="abs display" style="left:99px;top:218px;font-size:27px">WELCOME TO</div>
  <div class="abs display" style="left:99px;top:254px;font-size:54px;letter-spacing:2px">KESTREL YARD</div>
  <p class="abs body-copy" style="left:101px;top:320px;width:440px;font-size:14px;line-height:26px;color:#fff">A platform dedicated to making men wealthy, physically strong, mentally tough &amp; successful with women.</p>
  <div class="btn" style="left:99px;top:385px;width:142px;height:50px">Get Started</div>
  <div class="abs hero-art" role="img" aria-label="Smartphone rising over a glowing world map with gold coins and market charts"></div>
</section>

<!-- what we do -->
<section>
  <svg class="photo-hex" style="left:151px;top:570px" width="350" height="380" viewBox="0 0 350 380" role="img" aria-label="Smiling man pointing at a phone showing the platform app">
    <defs><linearGradient id="g1" x1="0" y1="0" x2="0" y2="1"><stop offset="0" stop-color="#6b4a30"/><stop offset="1" stop-color="#2a16c4"/></linearGradient></defs>
    <polygon points="190,70 345,150 345,290 190,375 25,290 25,150" fill="var(--accent)"/>
    <rect x="70" y="0" width="220" height="360" rx="20" fill="url(#g1)" opacity=".85"/>
  </svg>
  <span class="abs" style="left:504px;top:642px;width:20px;height:20px;border-radius:50%;background:var(--accent-bright)"></span>
  <div class="rule" style="left:606px;top:621px"></div>
  <h2 class="abs display" style="left:606px;top:634px;font-size:34px">WHAT WE DO</h2>
  <p class="abs body-copy" style="left:606px;top:688px;width:480px">Kestrel yard is a platform where you can learn everything you need about business, making money, crypto currency, fitness, health, mental toughness and resilience and how to be successful with women all in one place.</p>
  <p class="abs body-copy" style="left:606px;top:817px;width:480px">A platform dedicated to making men wealthy, physically strong, mentally tough &amp; successful with</p>
  <div class="btn" style="left:606px;top:892px;width:140px;height:51px">Read More</div>
</section>

<!-- affiliate -->
<section>
  <div class="rule" style="left:578px;top:1091px"></div>
  <h2 class="abs display center" style="top:1108px;font-size:34px">AFFILIATE SCHEME</h2>
  <p class="abs display center" style="top:1160px;font-size:21px;line-height:30px">EARN UP TO $125 DOLLARS PER PERSON WHO SIGNS UP<br>THROUGH YOUR LINK</p>
  <p class="abs body-copy" style="left:170px;top:1229px;width:860px;text-align:center">Itaque earum rerum hic tenetur a sapiente delectus, ut aut reiciendis voluptatibus occaecati cupiditate non provident, similique sunt in culpa qui officia deserunt mollitia maiores alias blanditiis praesentium voluptatum deleniti atque corruptconsequatur aut perferendis doloribus asperiores repellat.</p>
  <p class="abs body-copy" style="left:170px;top:1332px;width:860px;text-align:center">Neque porro quisquam est, qui dolorem ipsum quia dolor sit amet, consectetur, eum iure reprehenderit qui in ea voluptate velit esseadipisci velit, sed quia non numquam eius modim aliquam quaerat voluptatem.</p>
  <div class="btn" style="left:500px;top:1409px;width:200px;height:50px">Start Earning Now</div>
</section>

<!-- how it works -->
<section>
  <div class="rule" style="left:110px;top:1622px"></div>
  <h2 class="abs display" style="left:110px;top:1634px;font-size:34px;line-height:43px">HOW WILL THIS WORK<br>&amp; WHY SHOULD I BUY<br>POINTS?</h2>
  <p class="abs body-copy" style="left:111px;top:1760px;width:480px">Itaque earum rerum hic tenetur a sapiente delectus, ut aut reici endis voluptatibus maiores alias.</p>
  <p class="abs body-copy" style="left:111px;top:1838px;width:480px">Consequatur omnis voluptas assumenda est, omnis dolor aut perferendis doloribus asperiores repellat.</p>
  <div class="btn" style="left:111px;top:1907px;width:142px;height:50px">Learn More</div>
  <svg class="photo-hex" style="left:698px;top:1570px" width="330" height="385" viewBox="0 0 330 385" role="img" aria-label="Happy couple holding a payment card">
    <defs><linearGradient id="g2" x1="0" y1="0" x2="1" y2="0"><stop offset="0" stop-color="#6f8aa8"/><stop offset="1" stop-color="#e0b830"/></linearGradient></defs>
    <polygon points="160,75 320,160 320,300 160,385 0,300 0,160" fill="var(--accent)"/>
    <rect x="35" y="0" width="260" height="370" rx="20" fill="url(#g2)" opacity=".8"/>
  </svg>
  <span class="abs" style="left:1025px;top:1646px;width:22px;height:22px;border-radius:50%;background:var(--accent-bright)"></span>
</section>

<!-- buy points -->
<section>
  <div class="rule" style="left:578px;top:2089px"></div>
  <h2 class="abs display center" style="top:2104px;font-size:34px">BUY POINTS</h2>
  <p class="abs center" style="top:2149px;font-size:14.5px">A maximum of only $250 worth of points can be purchased per person until the platform goes fully live</p>
  <p class="abs body-copy" style="left:180px;top:2202px;width:840px;text-align:center;line-height:29px">Ut enim ad minima veniam, quis nostrum exercitationem ullam corporis suscipit laboriosam, nisi ut aliquid ex ea commodi consequatur? Quis autem vel eum iure reprehenderit qui in ea voluptate velit esse quam nihil molestiae consequatur, vel illum qui dolorem eum fugiat quo voluptas nulla pariatur.</p>
</section>

<!-- roadmap -->
<section>
  <div class="rule" style="left:578px;top:2444px"></div>
  <h2 class="abs display center" style="top:2458px;font-size:34px">ROAD MAP &amp; THE MODEL</h2>
  <p class="abs center" style="top:2520px;font-size:14.5px">It must have a very slick and sharp eye catching look, and be designed to convert people into purchasing points</p>
  <div class="btn" style="left:534px;top:2565px;width:132px;height:50px;font-size:18px;font-weight:600">2023</div>

  <svg class="abs" style="left:0;top:0" width="1200" height="4000" fill="none" stroke="var(--dots)" stroke-width="1.5" stroke-dasharray="2 3">
    <path d="M600 2615V2668H279V2739"/>
    <path d="M279 2987V3022H921V3047"/>
    <path d="M921 3296V3340H279V3373"/>
    <path d="M279 3621V3656H921V3681"/>
  </svg>

  <!-- Q1 -->
  <svg class="abs" style="left:146px;top:2734px" width="266" height="258" viewBox="0 0 266 258" role="img" aria-label="Card payment terminal icon">
    <polygon points="133,0 266,70 266,188 133,258 0,188 0,70" fill="var(--halo)"/>
    <polygon points="133,10 254,75 254,183 133,248 12,183 12,75" fill="var(--accent)"/>
    <g fill="none" stroke="#fff" stroke-width="4" stroke-linejoin="round">
      <rect x="68" y="55" width="72" height="150" rx="10"/><rect x="80" y="70" width="48" height="30"/>
      <rect x="128" y="105" width="50" height="90" rx="6"/><path d="M140 125h26M140 140h26"/>
      <path d="M84 120h8M100 120h8M84 140h8M100 140h8M84 160h8M100 160h8M84 180h8M100 180h8"/>
    </g>
  </svg>
  <div class="road-bar" style="left:436px;top:2800px"></div>
  <div class="road-text" style="left:457px;top:2802px">
    <div class="road-title">Questions 1</div>
    <div class="road-sub">Pre Buy In For Points</div>
    <div class="road-desc">Duis aute irure dolor in reprehenderit magni dolores eos qui ratione voluptate velit esse cillum dolore eu fugiat nulla pariatur.</div>
  </div>

  <!-- Q2 -->
  <svg class="abs" style="left:788px;top:3042px" width="266" height="258" viewBox="0 0 266 258" role="img" aria-label="Rocket launching from a laptop icon">
    <polygon points="133,0 266,70 266,188 133,258 0,188 0,70" fill="var(--halo)"/>
    <polygon points="133,10 254,75 254,183 133,248 12,183 12,75" fill="var(--accent)"/>
    <g fill="none" stroke="#fff" stroke-width="4" stroke-linejoin="round">
      <rect x="70" y="95" width="126" height="80" rx="4"/><path d="M55 175h156v8H55z"/>
      <path d="M133 50c14 14 18 38 12 70h-24c-6-32-2-56 12-70z"/><circle cx="133" cy="85" r="7"/>
      <path d="M105 160c10-14 46-14 56 0"/>
    </g>
  </svg>
  <div class="road-bar" style="left:756px;top:3110px"></div>
  <div class="road-text" style="left:90px;top:3110px;text-align:right">
    <div class="road-title">Questions 2</div>
    <div class="road-sub">Full Website Launch</div>
    <div class="road-desc">Excepteur sint occaecat cupidatat non proident, sunt in culpa qui officia deserunt mollit anim id est laborum.</div>
  </div>

  <!-- Q3 -->
  <svg class="abs" style="left:146px;top:3368px" width="266" height="258" viewBox="0 0 266 258" role="img" aria-label="Phone with rocket icon">
    <polygon points="133,0 266,70 266,188 133,258 0,188 0,70" fill="var(--halo)"/>
    <polygon points="133,10 254,75 254,183 133,248 12,183 12,75" fill="var(--accent)"/>
    <g fill="none" stroke="#fff" stroke-width="4" stroke-linejoin="round">
      <rect x="68" y="55" width="78" height="150" rx="12"/><path d="M95 192h24"/>
      <path d="M180 55c-4 30-22 52-50 62l-10-10c10-28 32-46 60-52z"/><circle cx="150" cy="150" r="5"/><circle cx="188" cy="185" r="6"/>
    </g>
  </svg>
  <div class="road-bar" style="left:436px;top:3435px"></div>
  <div class="road-text" style="left:457px;top:3437px">
    <div class="road-title">Questions 3</div>
    <div class="road-sub">App Launch</div>
    <div class="road-desc">Duis aute irure dolor in reprehenderit magni dolores eos qui ratione voluptate velit esse cillum dolore eu fugiat nulla pariatur.</div>
  </div>

  <!-- Q4 -->
  <svg class="abs" style="left:788px;top:3676px" width="266" height="258" viewBox="0 0 266 258" role="img" aria-label="Browser window with megaphone and rocket icon">
    <polygon points="133,0 266,70 266,188 133,258 0,188 0,70" fill="var(--halo)"/>
    <polygon points="133,10 254,75 254,183 133,248 12,183 12,75" fill="var(--accent)"/>
    <g fill="none" stroke="#fff" stroke-width="4" stroke-linejoin="round">
      <rect x="65" y="60" width="110" height="120" rx="6"/><path d="M65 80h110M78 70h4M88 70h4"/>
      <path d="M85 110h12l24-14v48l-24-14H85z"/>
      <path d="M170 70c16 12 22 40 16 80h-20c-6-40 0-68 4-80z"/><path d="M172 150v22M182 150v22"/>
    </g>
  </svg>
  <div class="road-bar" style="left:756px;top:3742px"></div>
  <div class="road-text" style="left:88px;top:3742px;text-align:right">
    <div class="road-title">Questions 4</div>
    <div class="road-sub">In App Advert Launch</div>
    <div class="road-desc">Excepteur sint occaecat cupidatat non proident, sunt in culpa qui officia deserunt mollit anim id est laborum.</div>
  </div>
</section>

<!-- footer -->
<footer class="footer">
  <div class="abs brand center" style="top:100px;font-size:38px;letter-spacing:2px">KESTREL YARD</div>
  <nav class="footer-links">
    <span>Home</span><span>What We Do</span><span>Why Choose Us</span><span>Testimonials</span><span>Roadmap</span><span>Contact Us</span>
  </nav>
  <div class="socials" aria-label="Social links">
    <span></span><span></span><span></span><span></span>
  </div>
  <p class="copyright">Copyrights@2022.Kestrel Yard.All Rights Reserved</p>
</footer>

</body>
</html>
```